Business Card Design Project

Looking to update our business cards. We have a logo with our slogan. We are an IT firm so we wouldlike a modern look.

Industry/Entity Type

Business

```html
<!DOCTYPE html>
<html lang="en">
<head>
<meta charset="utf-8">
<title>Kernova – Business Card</title>
<link rel="stylesheet" href="https://fonts.googleapis.com/css2?family=Questrial&family=Libre+Baskerville:wght@400;700&display=swap">
<style>
  :root {
    --backdrop: #ecebe6;
    --card: #ffffff;
    --brand-green: #5f7f3a;
    --accent-green: #a9c23f;
    --ink: #2b2b2b;
    --rule: #9a9a9a;
    --sans: "Questrial", Arial, sans-serif;
    --serif: "Libre Baskerville", Georgia, serif;
  }
  * { box-sizing: border-box; margin: 0; padding: 0; }
  html, body { width: 1200px; height: 693px; overflow: hidden; }
  body {
    background: var(--backdrop);
    position: relative;
    font-family: var(--serif);
    color: var(--ink);
  }
  .card {
    position: absolute;
    top: 186px;
    width: 520px;
    height: 320px;
    background: var(--card);
    border-radius: 90px 4px 90px 4px;
    box-shadow: 0 6px 18px rgba(0,0,0,0.12);
  }
  .card--front { left: 50px; }
  .card--back { left: 630px; }

  /* Front */
  .brand {
    position: absolute;
    top: 52px;
    left: 0;
    width: 100%;
    text-align: center;
  }
  .brand__name {
    font-family: var(--sans);
    font-size: 64px;
    letter-spacing: 10px;
    color: var(--brand-green);
    line-height: 1;
  }
  .brand__slogan {
    margin-top: 8px;
    font-family: var(--sans);
    font-size: 16px;
    letter-spacing: 4px;
    text-transform: uppercase;
    color: var(--ink);
    font-weight: 700;
  }
  .address {
    position: absolute;
    top: 178px;
    width: 100%;
    text-align: center;
    font-size: 14px;
    letter-spacing: 0.5px;
  }
  .person {
    position: absolute;
    top: 232px;
    left: 60px;
    width: 190px;
    text-align: right;
  }
  .person__name {
    font-size: 21px;
    font-weight: 700;
    color: var(--brand-green);
  }
  .person__title {
    font-size: 13px;
    color: var(--accent-green);
  }
  .divider {
    position: absolute;
    top: 212px;
    left: 266px;
    width: 1px;
    height: 84px;
    background: var(--rule);
  }
  .contacts {
    position: absolute;
    top: 210px;
    left: 280px;
    list-style: none;
    font-size: 13.5px;
    line-height: 21px;
  }
  .contacts li { display: flex; align-items: center; gap: 6px; }
  .contacts svg { width: 11px; height: 11px; fill: var(--brand-green); flex: none; }

  /* Back */
  .back-mark {
    position: absolute;
    top: 58px;
    left: 0;
    width: 100%;
    display: flex;
    flex-direction: column;
    align-items: center;
    gap: 16px;
  }
  .back-mark__dot {
    width: 110px;
    height: 110px;
    border-radius: 50%;
    background: var(--accent-green);
  }
  .back-mark__name {
    font-family: var(--sans);
    font-size: 34px;
    letter-spacing: 8px;
    color: var(--brand-green);
  }
  .web {
    position: absolute;
    bottom: 34px;
    width: 100%;
    text-align: center;
    font-family: var(--sans);
    font-size: 18px;
    letter-spacing: 6px;
    color: var(--ink);
  }
</style>
</head>
<body>
  <section class="card card--front" aria-label="Business card front">
    <header class="brand">
      <div class="brand__name">KERNOVA</div>
      <div class="brand__slogan">Making Technology Easy</div>
    </header>
    <p class="address">00, Complex name, City, State 0042</p>
    <div class="person">
      <div class="person__name">Your Name</div>
      <div class="person__title">Title</div>
    </div>
    <div class="divider"></div>
    <ul class="contacts">
      <li><svg viewBox="0 0 12 12" aria-hidden="true"><path d="M2.5 1 4.5 3.5 3.5 5C4.3 6.6 5.4 7.7 7 8.5L8.5 7.5 11 9.5 9.8 11C5.5 10.6 1.4 6.5 1 2.2Z"/></svg>0987 654321</li>
      <li><svg viewBox="0 0 12 12" aria-hidden="true"><rect x="3" y="0.5" width="6" height="11" rx="1.2"/></svg>0987 654321</li>
      <li><svg viewBox="0 0 12 12" aria-hidden="true"><path d="M1 2.5h10v7H1Z M1 2.5 6 6.5 11 2.5" stroke="#fff" stroke-width="0.8"/></svg>info@kernova.com</li>
      <li><svg viewBox="0 0 12 12" aria-hidden="true"><circle cx="6" cy="6" r="5"/><path d="M1 6h10M6 1c-2.5 3-2.5 7 0 10M6 1c2.5 3 2.5 7 0 10" stroke="#fff" stroke-width="0.7" fill="none"/></svg>www.kernova.com</li>
    </ul>
  </section>

  <section class="card card--back" aria-label="Business card back">
    <div class="back-mark">
      <div class="back-mark__dot"></div>
      <div class="back-mark__name">KERNOVA</div>
    </div>
    <p class="web">www.kernova.com</p>
  </section>
</body>
</html>
```